Tech Website

1. Overview
Prism48, formally named LumoVista, is a pioneer in computer vision technology and machine learning. Based out of Santa Clara, California, Prism48 is at the forefront of the User Interface revolution; building technology architecture that grants devices with the aptitude to respond to emotional detection, gaze tracking, facial recognition, age and gender identification and gaming interaction. Winner of the Mobile Track at NOVA Founders Sprint 2012, Prism48 has developed the next generation of consumer behaviour analytics. Prism48 software solutions are scalable across various platforms including mobile phone, tablets, PC and SmartTV.
Updates

Good day, 

Please see the update to our brief - there is a PDF of the type of format and design we are looking for.  It shows each page - Landing, Technology, Product, Press and Company.

Thank you for your designs

Regards,

Target Market(s)

Target market - A mix of enterprise and consumer audiences, targeting the need for the technology in the living room space

Industry/Entity Type

Architecture

Requirements
Must have
• Design preferences - Easy to navigate, modern with sleek feel, trendy, tech saavy, using cube as a consistent element/theme. colours are not determined, but parrot green was one idea with 2 additional underlying colours. keys words like user interface revolution or sense recognition are good sources to draw inspiration.

Landing page will have a video - illustrating different uses of technology

Technical Specs - Landing page, 6 tabs/subpages, and each subpage may have 1 or 2 additional pages. Coding will be necessary, not that much at the beginning stages.

```html
<!DOCTYPE html>
<html lang="en">
<head>
<meta charset="utf-8">
<title>Prism 48 – Home</title>
<link href="https://fonts.googleapis.com/css2?family=Play:wght@400;700&family=Arimo:wght@400;700&family=Oswald:wght@400&display=swap" rel="stylesheet">
<style>
:root{
  --green:#8cc425;
  --green-light:#b2de45;
  --green-dark:#6c9e12;
  --ink:#1c1c1c;
  --text:#3b3b3b;
  --muted:#888;
  --blue:#2c7cc2;
  --blue-btn:#2f86d6;
  --slate:#4a4f53;
  --player:#4e7a5a;
  --footer:#000;
  --rule:#cfcfcf;
}
*{box-sizing:border-box;margin:0;padding:0}
html,body{width:1200px;height:1187px;overflow:hidden;background:#fff}
body{position:relative;font-family:"Arimo",Arial,sans-serif;color:var(--text)}
.abs{position:absolute}

/* header */
.brand{left:145px;top:25px;display:flex;align-items:center;gap:18px}
.brand-mark{width:58px;height:56px;background:var(--green)}
.brand-name{font-family:"Play",sans-serif;font-size:35px;color:#3a3a3a;letter-spacing:.5px}
.search{left:860px;top:42px;width:197px;height:29px;border:1px solid #b9b9b9;border-radius:4px;background:linear-gradient(#f2f2f2,#fff)}
.search svg{position:absolute;right:8px;top:6px}

/* nav */
.nav{left:0;top:108px;width:1200px;height:52px;background:linear-gradient(var(--green-light),var(--green) 60%,var(--green-dark));border-top:1px solid #4e7a0c;border-bottom:2px solid #9fcf3a}
.nav-item{position:absolute;top:19px;font-family:"Oswald",sans-serif;font-size:15px;color:var(--ink);text-transform:uppercase}
.nav-item.active{left:144px;top:10px;width:58px;height:32px;background:#0c0c0c;color:#fff;border-radius:4px;text-align:center;line-height:32px}
.nav-social{position:absolute;top:18px;width:17px;height:17px;background:#1b1b1b;border-radius:3px}

.welcome{left:0;top:180px;width:1210px;text-align:center;font-family:"Play",sans-serif;font-size:31px;color:var(--ink)}

/* video stage */
.side-card{box-shadow:0 4px 10px rgba(0,0,0,.25)}
.side-left{left:145px;top:283px;width:120px;height:354px;background:linear-gradient(135deg,#dfe4ea,#b9c2cc 60%,#e8e8ea)}
.side-left .bar{position:absolute;left:0;bottom:0;width:100%;height:30px;background:#8e2a2a}
.side-right{left:922px;top:265px;width:131px;height:355px;background:linear-gradient(160deg,#8ea9c4,#cfd9e3 50%,#d8c6aa)}
.side-right .bar{position:absolute;left:0;bottom:0;width:100%;height:32px;background:#101010;color:#fff;font-size:10px;padding:11px 0 0 20px}
.main-video{left:259px;top:237px;width:668px;height:447px;box-shadow:0 6px 18px rgba(0,0,0,.35)}
.main-video .frame{width:100%;height:405px;background:radial-gradient(ellipse at 40% 40%,#b4b4b4,#8d8d8d 70%,#6f6f6f)}
.play-big{position:absolute;left:279px;top:148px;width:84px;height:84px;border-radius:50%;background:rgba(90,90,90,.75)}
.play-big svg{position:absolute;left:30px;top:22px}
.controls{position:absolute;left:0;top:405px;width:100%;height:42px;background:linear-gradient(#6a9471,var(--player));display:flex;align-items:center;color:#fff;font-size:13px}

/* features */
.thumb{width:280px;height:188px;background:#fff;box-shadow:0 2px 6px rgba(0,0,0,.3);padding:10px}
.thumb .shot{width:260px;height:150px;position:relative}
.thumb .shot1{background:linear-gradient(150deg,#c9ccd2,#8d939b 55%,#2f3238)}
.thumb .shot2{background:linear-gradient(120deg,#7d8fa3,#b7a59a 50%,#8a93a8)}
.thumb .play{position:absolute;left:110px;top:64px;width:40px;height:40px;border-radius:50%;background:#000}
.thumb .play svg{position:absolute;left:14px;top:11px}
.thumb .mini-bar{height:20px;background:#2a2a2a;display:flex;align-items:center;padding:0 6px;gap:6px;font-size:6px;color:#bbb}
.mini-bar .track{flex:1;height:3px;background:#eee}
.more-btn{width:163px;height:33px;background:var(--slate);border-radius:2px;color:#fff;font-family:"Oswald",sans-serif;font-size:15px;display:flex;align-items:center;padding-left:7px;gap:9px}
.more-btn .dot{width:19px;height:19px;border-radius:50%;background:#e6e6e6;position:relative}

.subscribe{left:743px;top:723px;width:302px;height:147px;border:1px solid #ddd;background:#fafafa;box-shadow:0 1px 3px rgba(0,0,0,.15);padding:13px 28px}
.subscribe h2{font-family:"Play",sans-serif;font-weight:400;font-size:18px;color:var(--blue)}
.subscribe p{font-size:11.5px;color:var(--muted);margin-top:12px;line-height:14px}
.subscribe .close{position:absolute;right:6px;top:5px;width:13px;height:13px;background:#e3e3e3}
.field{position:absolute;left:24px;top:84px;width:250px;height:40px;border:1px solid #ddd;background:#fff;font-size:11.5px;color:#777;padding:13px 10px}
.field .btn{position:absolute;right:4px;top:3px;width:85px;height:31px;background:linear-gradient(#4b9de6,var(--blue-btn));border:1px solid #2067a8;border-radius:3px;color:#123;text-align:center;line-height:29px;font-size:12px}

.join{left:744px;top:903px;width:299px;height:59px;background:linear-gradient(var(--green-light),var(--green-dark));color:#fff;box-shadow:0 1px 3px rgba(0,0,0,.2)}
.join .divider{position:absolute;left:56px;top:10px;width:1px;height:39px;background:rgba(255,255,255,.6)}
.join h3{position:absolute;left:70px;top:9px;font-family:"Play",sans-serif;font-size:19px;font-weight:700}
.join small{position:absolute;left:70px;top:33px;font-size:12.5px}

/* featured */
.featured-title{left:0;top:995px;width:1210px;text-align:center;font-family:"Play",sans-serif;font-size:20px;color:#555}
.rule{top:1009px;height:1px;background:var(--rule)}
.press{top:1046px;font-family:"Play",sans-serif;font-weight:700;font-size:33px}

/* footer */
.footer{left:0;top:1128px;width:1200px;height:59px;background:var(--footer)}
.footer-links{position:absolute;left:140px;top:20px;color:#fff;font-size:14px;word-spacing:4px}
.footer-links span{margin:0 9px;color:#ccc}
.footer-icons{position:absolute;left:860px;top:17px;display:flex;gap:6px}
.footer-icons i{width:24px;height:24px;border-radius:50%;background:#8a8a8a;display:block}
</style>
</head>
<body>

<header>
  <div class="abs brand"><div class="brand-mark"></div><span class="brand-name">Prism 48</span></div>
  <div class="abs search">
    <svg width="15" height="15" viewBox="0 0 15 15"><circle cx="6" cy="6" r="4.5" fill="none" stroke="#111" stroke-width="2"/><line x1="9.5" y1="9.5" x2="13.5" y2="13.5" stroke="#111" stroke-width="2.4"/></svg>
  </div>
</header>

<nav class="abs nav">
  <span class="nav-item active">Home</span>
  <span class="nav-item" style="left:233px">Technology</span>
  <span class="nav-item" style="left:356px">Product</span>
  <span class="nav-item" style="left:454px">Press</span>
  <span class="nav-item" style="left:531px">Company</span>
  <i class="nav-social" style="left:945px"></i>
  <i class="nav-social" style="left:976px"></i>
  <i class="nav-social" style="left:1007px"></i>
  <i class="nav-social" style="left:1039px"></i>
</nav>

<h1 class="abs welcome">Welcome to Prism 48</h1>

<section class="video-stage">
  <div class="abs side-card side-left" role="img" aria-label="Hand holding a tablet with floating media tiles">
    <div class="bar"></div>
  </div>
  <div class="abs side-card side-right" role="img" aria-label="Hands using a tablet showing a bar chart">
    <div class="bar">3.12 / 8.00</div>
  </div>
  <div class="abs main-video">
    <div class="frame" role="img" aria-label="Man in a suit using a tablet with floating letters and numbers"></div>
    <div class="play-big"><svg width="32" height="40" viewBox="0 0 32 40"><polygon points="0,0 32,20 0,40" fill="#fff"/></svg></div>
    <div class="controls">
      <svg style="margin-left:12px" width="20" height="18" viewBox="0 0 20 18"><polygon points="0,6 5,6 11,1 11,17 5,12 0,12" fill="#fff"/></svg>
      <div style="margin-left:8px;width:82px;height:6px;background:#fff;border-radius:3px;position:relative"><i style="position:absolute;right:2px;top:-3px;width:12px;height:12px;border-radius:50%;background:#bbb"></i></div>
      <svg style="margin-left:32px" width="16" height="16" viewBox="0 0 16 16"><polygon points="0,0 16,8 0,16" fill="#fff"/></svg>
      <div style="margin-left:16px;width:332px;height:12px;background:#fff;border-radius:6px;position:relative;overflow:hidden"><i style="position:absolute;left:2px;top:2px;width:162px;height:8px;background:#000;border-radius:4px"></i></div>
      <span style="margin-left:12px">3.12 / 8.00</span>
      <svg style="margin-left:40px" width="18" height="18" viewBox="0 0 18 18"><path d="M0 0h6v2H2v4H0zM12 0h6v6h-2V2h-4zM0 12h2v4h4v2H0zM16 12h2v6h-6v-2h4z" fill="#fff"/></svg>
    </div>
  </div>
</section>

<section class="features">
  <div class="abs thumb" style="left:141px;top:723px">
    <div class="shot shot1" role="img" aria-label="Finger touching a tablet showing business news">
      <div class="play"><svg width="14" height="18" viewBox="0 0 14 18"><polygon points="0,0 14,9 0,18" fill="#fff"/></svg></div>
    </div>
    <div class="mini-bar"><span>▶</span><div class="track"></div><span>0:10 / 0:10</span></div>
  </div>
  <a class="abs more-btn" style="left:189px;top:929px">See More Features <span class="dot"></span></a>

  <div class="abs thumb" style="left:440px;top:723px">
    <div class="shot shot2" role="img" aria-label="Presenter pointing at a wall map">
      <div class="play"><svg width="14" height="18" viewBox="0 0 14 18"><polygon points="0,0 14,9 0,18" fill="#fff"/></svg></div>
    </div>
    <div class="mini-bar"><span>▶</span><div class="track"></div><span>0:10 / 0:10</span></div>
  </div>
  <a class="abs more-btn" style="left:488px;top:929px">See More Features <span class="dot"></span></a>

  <div class="abs subscribe">
    <i class="close"></i>
    <h2>Subscribe to Prism 48 Blog</h2>
    <p>Enter your email address to receive all news<br>from our awesome website.</p>
    <div class="field">Your email address...<span class="btn">Subscribe</span></div>
  </div>

  <div class="abs join">
    <svg style="position:absolute;left:20px;top:21px" width="18" height="17" viewBox="0 0 18 17"><path d="M1 1l7 7.5-7 7.5M9 1l7 7.5-7 7.5" fill="none" stroke="#fff" stroke-width="3"/></svg>
    <i class="divider"></i>
    <h3>Join Us Live At Prism 48</h3>
    <small>NEXCON 2013 Jan 8-11</small>
  </div>
</section>

<section class="featured">
  <div class="abs rule" style="left:129px;width:387px"></div>
  <div class="abs rule" style="left:688px;width:388px"></div>
  <h2 class="abs featured-title" style="font-weight:400">As Featured In</h2>
  <span class="abs press" style="left:145px;color:#2a2a2a">Lumen Daily</span>
  <span class="abs press" style="left:345px;color:#6a1b91">Orbitly</span>
  <span class="abs press" style="left:515px;color:#3d86c6">Signalcast</span>
  <span class="abs press" style="left:735px;color:#c4161c">NWB</span>
  <span class="abs press" style="left:860px;color:#b71c22;font-size:28px;top:1050px">Circuit Review</span>
</section>

<footer class="abs footer">
  <div class="footer-links">Home<span>|</span>Technology<span>|</span>Product<span>|</span>Press<span>|</span>Company</div>
  <div class="footer-icons"><i></i><i></i><i></i><i></i><i></i><i></i><i></i></div>
</footer>

</body>
</html>
```